Non fiction leadership Book Cover design needed for “Stay Bold: Build On Lasting Discipline”

I need a front cover design for a new book 6 X 9 traditional non-fiction book.

Title: "Stay BOLD - Build On Lasting Discipline"

The subtitle is not finalized- so use 2 lines of smaller dummy text

My brand guide is attached (please use the tan color sparingly)

I'd like to see BOLD look like it is in motion and "flying" across the page

Need CREATIVE designs and options

Do not want my picture on the front cover - I do want it on the back cover.

On the front cover I’d like to see creative use of font to create movement on “BOLD”

Target Market(s)

Business leaders

Industry/Entity Type

Aviation

Font styles to use
Other font styles liked:
• See style guide- can add additional font (modern script or san serif)

Colors
0054AA
0677BA
7BADD7
CADEEF
E8F1F8
EB3D1F
EC4F4E
F09395
F8D3D4
FCEDEE

Requirements
Must have
• Creative font use, using perspective to create movement/motion on BOLD
Should not have
• My picture on the front cover- my picture should be on the back cover

```html
<!DOCTYPE html>
<html lang="en">
<head>
<meta charset="utf-8">
<title>Stay Bold: Build On Lasting Discipline – Front Cover</title>
<link href="https://fonts.googleapis.com/css2?family=Archivo+Black&family=Roboto+Condensed:wght@700&family=Montserrat:wght@700&family=Nunito+Sans:wght@400&family=Oswald:wght@600&display=swap" rel="stylesheet">
<style>
  :root {
    --stage: #f1f1f1;
    --paper: #ffffff;
    --ink: #1c1a1d;
    --red: #b81f29;
    --red-bright: #e0242f;
    --tan-dark: #9c6434;
    --tan-mid: #c98f55;
    --tan-light: #e3ba84;
  }
  * { box-sizing: border-box; margin: 0; padding: 0; }
  html, body {
    width: 1200px;
    height: 800px;
    overflow: hidden;
    background: var(--stage);
  }
  .stage {
    position: relative;
    width: 1200px;
    height: 800px;
  }
  .cover {
    position: absolute;
    left: 360px;
    top: 40px;
    width: 480px;
    height: 720px;
    background: var(--paper);
    overflow: hidden;
    box-shadow: 0 10px 30px rgba(0,0,0,0.12);
  }
  .cover-shapes {
    position: absolute;
    inset: 0;
  }
  .plane-art {
    position: absolute;
    left: 300px;
    top: 22px;
    width: 150px;
    height: 66px;
    transform: rotate(-28deg);
    background: linear-gradient(120deg, #ffffff 0%, #f3d6d8 55%, var(--red-bright) 100%);
    border-radius: 4px;
  }
  .title {
    position: absolute;
    left: 40px;
    top: 138px;
    width: 270px;
    color: var(--ink);
  }
  .title-kicker {
    font-family: "Archivo Black", sans-serif;
    font-size: 40px;
    line-height: 1;
    margin-left: 44px;
    letter-spacing: 0.5px;
  }
  .title-main {
    display: inline-block;
    font-family: "Archivo Black", sans-serif;
    font-weight: 400;
    line-height: 0.92;
    color: var(--red);
    letter-spacing: -2px;
    white-space: nowrap;
    transform: skewX(-12deg);
    transform-origin: left bottom;
  }
  .title-main .letter {
    display: inline-block;
    vertical-align: baseline;
  }
  .title-main .letter-1 { font-size: 56px; opacity: 0.75; }
  .title-main .letter-2 { font-size: 66px; opacity: 0.85; }
  .title-main .letter-3 { font-size: 76px; opacity: 0.93; }
  .title-main .letter-4 { font-size: 88px; }
  .title-tagline {
    font-family: "Roboto Condensed", sans-serif;
    font-weight: 700;
    font-size: 18px;
    margin-top: 8px;
    letter-spacing: 0.2px;
    white-space: nowrap;
  }
  .subtitle-block {
    position: absolute;
    left: 40px;
    top: 402px;
    width: 300px;
  }
  .subtitle {
    font-family: "Roboto Condensed", sans-serif;
    font-weight: 700;
    font-size: 35px;
    line-height: 1.02;
    color: var(--ink);
  }
  .secondary-title {
    font-family: "Montserrat", sans-serif;
    font-weight: 700;
    font-size: 13.5px;
    color: var(--red);
    margin-top: 6px;
  }
  .body-copy {
    font-family: "Nunito Sans", sans-serif;
    font-size: 13px;
    line-height: 1.35;
    color: var(--ink);
    margin-top: 8px;
    width: 250px;
  }
  .author-bar {
    position: absolute;
    left: 0;
    top: 600px;
    width: 480px;
    height: 70px;
  }
  .author-tab {
    position: absolute;
    left: 0;
    top: 4px;
    width: 16px;
    height: 44px;
    background: linear-gradient(90deg, var(--tan-dark), var(--tan-light));
  }
  .author-name {
    position: absolute;
    left: 36px;
    top: 0;
    font-family: "Oswald", sans-serif;
    font-weight: 600;
    font-size: 26px;
    line-height: 1.05;
    color: var(--tan-dark);
    letter-spacing: 1px;
    text-transform: uppercase;
  }
  .author-name .surname {
    display: block;
    font-size: 15px;
    letter-spacing: 7px;
  }
  .author-band {
    position: absolute;
    left: 212px;
    top: 12px;
    width: 268px;
    height: 50px;
    background: linear-gradient(90deg, var(--tan-dark), var(--tan-mid) 60%, var(--tan-light));
  }
</style>
</head>
<body>
  <main class="stage">
    <article class="cover">
      <svg class="cover-shapes" viewBox="0 0 480 720" width="480" height="720" aria-hidden="true">
        <path class="sky-arc" fill="var(--red)"
              d="M0,0 L480,0 L480,58 C440,70 400,86 350,100 C300,112 250,118 200,112 C120,102 50,60 0,10 Z"/>
        <path class="flight-curve" fill="var(--red)"
              d="M480,58 C400,90 335,140 325,230 C315,330 380,420 480,462 Z"/>
      </svg>

      <div class="plane-art" role="img" aria-label="Paper plane in white and red, flying up to the right"></div>

      <header class="title">
        <p class="title-kicker">STAY</p>
        <h1 class="title-main" aria-label="BOLD"><span class="letter letter-1">B</span><span class="letter letter-2">O</span><span class="letter letter-3">L</span><span class="letter letter-4">D</span></h1>
        <p class="title-tagline">BUILD ON LASTING DISCIPLINE</p>
      </header>

      <section class="subtitle-block">
        <h2 class="subtitle">SUBTITLE<br>PLACEHOLDER</h2>
        <p class="secondary-title">Smaller Secondary Title Placeholder</p>
        <p class="body-copy">Nunito Sans Font Family for All Body Copy - Lorem ipsum dolor sit amet, consectetur adipiscing elit.</p>
      </section>

      <footer class="author-bar">
        <span class="author-tab"></span>
        <p class="author-name">Marian<span class="surname">Holloway</span></p>
        <span class="author-band"></span>
      </footer>
    </article>
  </main>
</body>
</html>
```